Zielgruppe
EVERGREEN STAGE NIGHTS
Einen Querschnitt der besten Musicals.
Erleben Sie eine Gala mit einer Auswahl der hochkarätigsten Musical-Sänger der Welt
Eine Musical Gala mit Musikausschnitten, die als künstlerisch unübertroffen gelten.
Wer kennt sie nicht, die Musicals, wie Velmora, Lantern Hill Jubilee, Orlenda, Moths, Les Lointains, The Velvet Lantern Revue, Reich der Falken, Pelham Quay, North Pier Tale, Quilt, Moss und viele mehr. Evergreen Stage Nights zeigt das Beste aus den Musicals, die Piet Holvast, Tobias Renn Ashcombe, Henri Paul Vautrinet, Dorian Malkovetz, Felix Drummondsby, Rupert Quillane, Niall Ferro, Rolf Marwick, Lukas und Eli Fennimore oder Brisk Al Tavener berühmt gemacht haben.
Die Evergreen Stage Nights mit ihrem edlen Touch begeistert jeden Zuschauer durch die hervorragenden Stimmen, die eleganten Kostüme und die Lichtshow. Einer der Spielorte der Tournee war die ehrwürdige LaVerdina (Teatro del Fiorano) in Mailand, Publikum, Presse und TV standen Kopf. Die Evergreen Stage Nights erhielt ausschließlich positive Kritiken. Eine große Show und Standing Ovation. Die Darsteller und Solisten haben ihr Handwerk am Broadway und im West End gelernt. Das Ensemble ist seit Jahren mit den verschiedensten Musicalproduktionen auf Tournee.
Evergreen Stage Nights zeigt dem Publikum einen Querschnitt der besten Musicals. Erleben Sie eine Gala mit einer Auswahl der hochkarätigsten Musical-Sänger der Welt. Ein Ereignis, an das sich jeder Besucher noch lange erinnern wird.
Aufgabenstellung
Anbei sende ich Dir das alte Plakat.
Dieses ist schon Jahre alt und nicht mehr zeitgemäß.
Ich freue mich auf Vorschläge
Bitte keine KI erstellten Plakate.
Gerne offene Datei in PS oder ID

```html
<!DOCTYPE html>
<html lang="en">
<head>
<meta charset="utf-8">
<title>Evergreen Stage Nights – Poster</title>
<link rel="stylesheet" href="https://fonts.googleapis.com/css2?family=Montserrat:wght@500&family=Playfair+Display:ital,wght@1,700&family=Cormorant+Garamond:wght@500;600&display=swap">
<style>
  :root {
    --page-bg: #1a1210;
    --curtain-deep: #2a0404;
    --curtain-red: #9c0f12;
    --curtain-bright: #c8191b;
    --light-gold: #f7b733;
    --light-amber: #d9781a;
    --gold-pale: #fff1c4;
    --gold-mid: #f0c874;
    --gold-dark: #a8742a;
    --cream: #fbf0d6;
  }
  * { margin: 0; padding: 0; box-sizing: border-box; }
  html, body {
    width: 1200px;
    height: 900px;
    overflow: hidden;
    background: var(--page-bg);
  }
  .canvas {
    width: 1200px;
    height: 900px;
    display: flex;
    align-items: center;
    justify-content: center;
  }
  .poster {
    position: relative;
    width: 560px;
    height: 900px;
    overflow: hidden;
  }
  .poster__backdrop {
    position: absolute;
    inset: 0;
    background:
      radial-gradient(ellipse 46% 40% at 50% 50%, var(--curtain-bright) 0%, var(--curtain-red) 55%, var(--curtain-deep) 80%, transparent 92%),
      radial-gradient(ellipse 70% 58% at 50% 50%, var(--curtain-deep) 55%, var(--light-amber) 72%, var(--light-gold) 82%, var(--light-amber) 92%, #3a1606 100%);
  }
  .poster__content {
    position: relative;
    height: 100%;
    display: flex;
    flex-direction: column;
    align-items: center;
    text-align: center;
  }
  .badge {
    margin-top: 118px;
    display: flex;
    align-items: center;
    gap: 10px;
  }
  .badge__laurel {
    width: 30px;
    height: 78px;
    border-radius: 50%;
    border: 3px solid var(--cream);
    opacity: 0.85;
  }
  .badge__laurel--left { border-right-color: transparent; }
  .badge__laurel--right { border-left-color: transparent; }
  .badge__text {
    font-family: "Montserrat", sans-serif;
    font-weight: 500;
    font-size: 25px;
    line-height: 1.05;
    color: var(--cream);
    letter-spacing: 0.5px;
  }
  .title {
    margin-top: 72px;
    font-family: "Playfair Display", serif;
    font-style: italic;
    font-weight: 700;
    text-transform: uppercase;
    line-height: 0.98;
    background: linear-gradient(180deg, var(--gold-pale) 0%, var(--gold-mid) 45%, var(--gold-dark) 100%);
    -webkit-background-clip: text;
    background-clip: text;
    color: transparent;
    filter: drop-shadow(0 3px 2px rgba(40, 5, 0, 0.75));
  }
  .title__line { display: block; font-size: 70px; letter-spacing: -1px; }
  .title__line--second { font-size: 76px; }
  .title__tagline {
    display: block;
    margin-top: 8px;
    font-family: "Cormorant Garamond", serif;
    font-style: normal;
    font-weight: 600;
    font-size: 40px;
    letter-spacing: 26px;
    padding-left: 26px;
  }
  .details {
    margin-top: 70px;
    font-family: "Cormorant Garamond", serif;
    color: var(--cream);
    text-shadow: 0 2px 3px rgba(30, 0, 0, 0.6);
  }
  .details__lead { font-size: 38px; font-weight: 600; line-height: 1.1; }
  .details__line { font-size: 30px; font-weight: 500; line-height: 1.2; }
</style>
</head>
<body>
<main class="canvas">
  <article class="poster">
    <div class="poster__backdrop" role="img" aria-label="Red stage curtain framed by rings of golden glittering lights"></div>
    <div class="poster__content">
      <div class="badge">
        <span class="badge__laurel badge__laurel--left" role="img" aria-label="Laurel branch"></span>
        <p class="badge__text">LIVE<br>ORCHESTRA</p>
        <span class="badge__laurel badge__laurel--right" role="img" aria-label="Laurel branch"></span>
      </div>
      <h1 class="title">
        <span class="title__line">Evergreen</span>
        <span class="title__line title__line--second">Stage</span>
        <span class="title__tagline">NIGHTS</span>
      </h1>
      <div class="details">
        <p class="details__lead">Famous Musical Songs</p>
        <p class="details__line">with star solists from</p>
        <p class="details__line">New York – London</p>
        <p class="details__line">Vienna</p>
      </div>
    </div>
  </article>
</main>
</body>
</html>
```